Stonebridge Building and Projects business cards

A business card with watermark background (construction work)

Company logo attached

Home improvement projects
House renovations
Bathroom and kitchen renovations
House extensions
New builds and granny flats

Director Omar Haddani
(Phone number)
omar@sbpbuilding.com.au
(Instagram logo) sbp_building

```html
<!DOCTYPE html>
<html lang="en">
<head>
<meta charset="utf-8">
<title>Stonebridge Building and Projects – Business Cards</title>
<link rel="stylesheet" href="https://fonts.googleapis.com/css2?family=Arimo:wght@400&family=Montserrat:wght@500;600&display=swap">
<style>
  :root {
    --brand-blue: #3178b6;
    --frost: #ece5e3;
    --divider: #474747;
    --ink-light: #ffffff;
    --page: #dcd6d4;
    --faint: rgba(49, 120, 182, 0.22);
  }
  * { box-sizing: border-box; margin: 0; padding: 0; }
  html, body { width: 1200px; height: 1181px; overflow: hidden; }
  body {
    background: var(--page);
    position: relative;
    font-family: "Arimo", Arial, sans-serif;
    color: var(--ink-light);
  }
  .card {
    position: absolute;
    width: 654px;
    height: 403px;
    display: flex;
    box-shadow: 0 6px 18px rgba(0, 0, 0, 0.12);
  }
  .card--front { left: 180px; top: 156px; }
  .card--back  { left: 480px; top: 627px; }

  .panel { height: 100%; position: relative; }
  .panel--blue { background: var(--brand-blue); width: 332px; }
  .panel--frost { background: var(--frost); flex: 1; }
  .divider { width: 4px; background: var(--divider); height: 100%; }

  /* front: contact side */
  .contact { padding: 82px 0 0 26px; }
  .contact__name {
    font-family: "Montserrat", Arial, sans-serif;
    font-weight: 600;
    font-size: 26px;
    line-height: 1;
  }
  .contact__role { font-size: 18px; margin-top: 4px; }
  .contact__social {
    display: flex; align-items: center; gap: 7px;
    font-size: 18px; margin-top: 48px;
  }
  .contact__social .mark {
    width: 22px; height: 22px; border-radius: 5px; background: var(--ink-light);
  }
  .contact__list { list-style: none; margin-top: 43px; font-size: 18.5px; }
  .contact__list li { display: flex; align-items: center; gap: 6px; height: 24px; }
  .contact__list svg { width: 18px; height: 18px; flex: none; }

  /* brand name lockup */
  .brand {
    position: absolute; inset: 0;
    display: flex; flex-direction: column; align-items: center; justify-content: center;
    font-family: "Montserrat", Arial, sans-serif;
    font-weight: 500;
    color: var(--brand-blue);
    text-align: center;
    line-height: 1.15;
  }
  .brand__name { font-size: 34px; }
  .brand__sub { font-size: 19px; }
  .brand--ghost { color: var(--faint); transform: scaleX(-1); padding-top: 30px; }

  /* back: services */
  .services {
    list-style: none;
    padding-top: 120px;
    padding-right: 19px;
    text-align: right;
    font-size: 18.5px;
  }
  .services li {
    height: 35px;
    display: flex; justify-content: flex-end; align-items: center; gap: 6px;
  }
  .services li::after {
    content: ""; width: 8px; height: 8px; border-radius: 50%;
    background: var(--ink-light);
  }
</style>
</head>
<body>

  <section class="card card--front" aria-label="Card front">
    <div class="panel panel--blue contact">
      <h1 class="contact__name">Omar Haddani</h1>
      <p class="contact__role">Director</p>
      <p class="contact__social"><span class="mark" aria-hidden="true"></span>sbp_building</p>
      <ul class="contact__list">
        <li>
          <svg viewBox="0 0 24 24" aria-hidden="true"><path fill="#fff" d="M6.6 10.8a15.1 15.1 0 0 0 6.6 6.6l2.2-2.2c.3-.3.7-.4 1-.2 1.1.4 2.3.6 3.6.6.6 0 1 .4 1 1V20c0 .6-.4 1-1 1A17 17 0 0 1 3 4c0-.6.4-1 1-1h3.5c.6 0 1 .4 1 1 0 1.3.2 2.5.6 3.6.1.3 0 .7-.2 1z"/></svg>
          044-987 650 213
        </li>
        <li>
          <svg viewBox="0 0 24 24" aria-hidden="true"><rect x="2" y="5" width="20" height="14" fill="#fff"/><path d="M2 5l10 8 10-8" fill="none" stroke="#3178b6" stroke-width="1.6"/></svg>
          omar@sbpbuilding.com.au
        </li>
        <li>
          <svg viewBox="0 0 24 24" aria-hidden="true" fill="none" stroke="#fff" stroke-width="1.6"><circle cx="12" cy="12" r="9.5"/><ellipse cx="12" cy="12" rx="4.2" ry="9.5"/><path d="M2.5 12h19M4 7h16M4 17h16M12 2.5v19"/></svg>
          www.sbpbuilding.com.au
        </li>
      </ul>
    </div>
    <div class="divider"></div>
    <div class="panel panel--frost">
      <div class="brand">
        <span class="brand__name">Stonebridge</span>
        <span class="brand__sub">Building and Projects</span>
      </div>
    </div>
  </section>

  <section class="card card--back" aria-label="Card back">
    <div class="panel panel--frost">
      <div class="brand brand--ghost" aria-hidden="true">
        <span class="brand__name">Stonebridge</span>
        <span class="brand__sub">Building and Projects</span>
      </div>
    </div>
    <div class="divider"></div>
    <div class="panel panel--blue">
      <ul class="services">
        <li>Home improvement projects</li>
        <li>House renovations</li>
        <li>House extensions</li>
        <li>New builds and granny flats</li>
        <li>Bathroom and kitchen renovations</li>
      </ul>
    </div>
  </section>

</body>
</html>
```